Garlic Farm for Farm Sales/Restaurant sales

Need a professional, but appealing to agriculture world. We are selling 27 kinds of Organic Garlic from a farm in Simla,CO. I have uploaded logo and business information-we are going to need a template, because I will need to use it for four separate people.
-We are trying to appeal to Farm to table restaurants
-As well as growers/farmers

Target Market(s)

Agriculture Sales/Restaurants-Organic

Industry/Entity Type

Agriculture

Contact Information for Business Card

Want it to look more unique then your average kelto stock card- I want it to look amazing

Font styles to use
Sans Serif

Colors
0455a3
ec1f27
fbed22
ffffff

Requirements
Must have
• Just be creative
Nice to have
• Colorful
Should not have
• plain

```html
<!DOCTYPE html>
<html lang="en">
<head>
<meta charset="utf-8">
<title>Summit Clove – Business Card</title>
<link rel="stylesheet" href="https://fonts.googleapis.com/css2?family=Open+Sans:wght@400;600&display=swap">
<style>
  :root {
    --navy: #1d3866;
    --red: #c0092a;
    --red-soft: #cf2a45;
    --ink: #4a4a4a;
    --paper: #ffffff;
    --backdrop: #e9e6e1;
  }
  html, body {
    margin: 0;
    padding: 0;
    width: 1200px;
    height: 987px;
    overflow: hidden;
    background: var(--backdrop);
    font-family: "Open Sans", Arial, sans-serif;
  }
  .card {
    position: absolute;
    left: 292px;
    width: 616px;
    height: 352px;
    box-shadow: 0 2px 6px rgba(0,0,0,0.25);
    overflow: hidden;
  }
  .card--front { top: 130px; background: var(--paper); }
  .card--back  { top: 506px; background: var(--red); }

  .brand {
    position: absolute;
    display: flex;
    align-items: center;
    gap: 12px;
    font-weight: 600;
    white-space: nowrap;
  }
  .brand__dot { border-radius: 50%; flex: none; }

  .card--front .brand {
    right: 30px;
    top: 110px;
    font-size: 34px;
    color: var(--navy);
  }
  .card--front .brand__dot { width: 26px; height: 26px; background: var(--red); }

  .holder {
    position: absolute;
    left: 35px;
    top: 170px;
  }
  .holder__name {
    margin: 0;
    font-size: 21px;
    font-weight: 600;
    color: var(--navy);
    letter-spacing: 0.3px;
  }
  .holder__role {
    margin: 2px 0 0;
    font-size: 15px;
    color: var(--red);
  }
  .divider {
    position: absolute;
    left: 35px;
    right: 30px;
    top: 244px;
    height: 1px;
    background: var(--red);
  }
  .contacts {
    position: absolute;
    left: 35px;
    top: 256px;
    margin: 0;
    padding: 0;
    list-style: none;
    font-size: 15px;
    color: var(--ink);
  }
  .contacts li {
    display: flex;
    align-items: center;
    gap: 8px;
    height: 23.5px;
  }
  .contacts svg { width: 14px; height: 14px; fill: var(--navy); flex: none; }
  .address {
    position: absolute;
    right: 30px;
    top: 280px;
    margin: 0;
    text-align: right;
    font-size: 15px;
    line-height: 23.5px;
    font-style: normal;
    color: var(--ink);
  }
  .edge-band { position: absolute; left: 0; bottom: 0; width: 616px; height: 12px; }

  .card--back .brand {
    left: 50%;
    top: 150px;
    transform: translateX(-50%);
    font-size: 46px;
    color: var(--paper);
  }
  .card--back .brand__dot { width: 34px; height: 34px; background: var(--red-soft); }
  .social {
    position: absolute;
    left: 50%;
    top: 280px;
    transform: translateX(-50%);
    display: flex;
    gap: 5px;
  }
  .social span {
    width: 22px;
    height: 22px;
    border: 1.5px solid var(--paper);
    border-radius: 50%;
    box-sizing: border-box;
  }
</style>
</head>
<body>

<section class="card card--front" aria-label="Business card front">
  <div class="brand"><span class="brand__dot"></span>Summit Clove</div>

  <div class="holder">
    <h1 class="holder__name">DANA WHITFORD</h1>
    <p class="holder__role">CEO/FOUNDER</p>
  </div>
  <div class="divider"></div>

  <ul class="contacts">
    <li>
      <svg viewBox="0 0 24 24" aria-hidden="true"><path d="M6.6 10.8a15.1 15.1 0 0 0 6.6 6.6l2.2-2.2a1 1 0 0 1 1-.25 11.4 11.4 0 0 0 3.6.57 1 1 0 0 1 1 1V20a1 1 0 0 1-1 1A17 17 0 0 1 3 4a1 1 0 0 1 1-1h3.5a1 1 0 0 1 1 1c0 1.25.2 2.45.57 3.57a1 1 0 0 1-.25 1z"/></svg>
      719-555-0148
    </li>
    <li>
      <svg viewBox="0 0 24 24" aria-hidden="true"><path d="M2 5h20v14H2z M2 5l10 8 10-8" fill="none" stroke="#1d3866" stroke-width="2.4"/></svg>
      dana@summitclove.com
    </li>
    <li>
      <svg viewBox="0 0 24 24" aria-hidden="true"><circle cx="12" cy="12" r="10"/><path d="M2 12h20M12 2c3 3 3 17 0 20M12 2c-3 3-3 17 0 20" fill="none" stroke="#fff" stroke-width="1.4"/></svg>
      www.summitclove.com
    </li>
  </ul>

  <address class="address">P.O. Box 12 Ridgeview<br>CO&nbsp; 80999</address>

  <svg class="edge-band" viewBox="0 0 616 12" preserveAspectRatio="none" aria-hidden="true">
    <polygon points="0,0 400,0 396,12 0,12" fill="var(--navy)"/>
    <polygon points="404,0 616,0 616,12 400,12" fill="var(--red)"/>
  </svg>
</section>

<section class="card card--back" aria-label="Business card back">
  <div class="brand"><span class="brand__dot"></span>Summit Clove</div>
  <div class="social" aria-label="Social links">
    <span></span><span></span><span></span><span></span>
  </div>
</section>

</body>
</html>
```